Business Card for Coastal Tundrabridge Advisory

We need a business card for Coastal Tundrabridge Advisory. The company website address is provided below. The company logo is attached. We provide specialized permafrost services to the mining, transportation, and oil & gas industries. The card should be prepared for:
Matthias Korhonen, PhD.
Coastal Tundrabridge Advisory
PO Box 418259
Quillwater, Alaska 99642
Direct: +1-907-555-0143
Email: mkorhonen@tundrabridgeadvisory.example
Website: www.coastaltundrabridgeadvisory.example

```html
<!DOCTYPE html>
<html lang="en">
<head>
<meta charset="utf-8">
<title>Coastal Tundrabridge Advisory – Business Card</title>
<link rel="stylesheet" href="https://fonts.googleapis.com/css2?family=Roboto:wght@300;400;500;700&display=swap">
<style>
  :root {
    --backdrop: #222222;
    --card: #0f1621;
    --ink: #ffffff;
    --ink-soft: #d9dde3;
    --emboss: #1a2331;
    --rule: rgba(255,255,255,0.7);
  }
  * { margin: 0; padding: 0; box-sizing: border-box; }
  html, body {
    width: 1200px; height: 780px; overflow: hidden;
    background: var(--backdrop);
    font-family: "Roboto", Arial, sans-serif;
    color: var(--ink);
  }
  .sheet {
    width: 1200px; height: 780px;
    display: flex; align-items: center; justify-content: center; gap: 40px;
  }
  .card {
    position: relative;
    width: 530px; height: 303px;
    background: var(--card);
    overflow: hidden;
  }

  /* Front */
  .brand {
    position: absolute; left: 34px; top: 118px; width: 190px;
    font-weight: 500; font-size: 20px; line-height: 1.25;
    letter-spacing: 0.06em; text-transform: uppercase; color: var(--ink);
  }
  .divider {
    position: absolute; left: 250px; top: 40px;
    width: 1px; height: 130px;
    background: linear-gradient(to bottom, transparent, var(--rule), transparent);
  }
  .person { position: absolute; left: 272px; top: 44px; }
  .person-name { font-size: 22px; line-height: 1.1; white-space: nowrap; }
  .person-name .given { font-weight: 700; }
  .person-name .family { font-weight: 300; }
  .person-degree { font-size: 13px; font-weight: 500; margin-top: 2px; }
  .contacts { list-style: none; margin-top: 14px; }
  .contacts li {
    display: flex; align-items: center; gap: 7px;
    font-size: 9.5px; color: var(--ink-soft); line-height: 1.75; white-space: nowrap;
  }
  .contacts svg { width: 10px; height: 10px; flex: none; }
  .address {
    position: absolute; right: 26px; bottom: 26px;
    font-size: 12px; color: var(--ink-soft);
  }

  /* Back */
  .brand-large {
    position: absolute; left: 0; right: 0; top: 82px;
    text-align: center;
    font-weight: 500; font-size: 30px; letter-spacing: 0.08em;
    text-transform: uppercase; line-height: 1.2; color: var(--emboss);
  }
  .services { position: absolute; left: 0; right: 0; bottom: 32px; text-align: center; }
  .services-title { font-size: 12px; font-weight: 700; letter-spacing: 0.02em; }
  .services-text { font-size: 10.5px; color: var(--ink-soft); margin-top: 4px; }
</style>
</head>
<body>
<main class="sheet">
  <section class="card card-front">
    <div class="brand">Coastal Tundrabridge Advisory</div>
    <div class="divider"></div>
    <div class="person">
      <h1 class="person-name"><span class="given">Matthias</span> <span class="family">Korhonen</span></h1>
      <p class="person-degree">PhD</p>
      <ul class="contacts">
        <li>
          <svg viewBox="0 0 10 10" aria-hidden="true"><path d="M2 1l2 2-1 1.2c.6 1.2 1.5 2.1 2.8 2.8L7 6l2 2-1.3 1.3C4.8 9 1 5.2.7 2.3z" fill="#fff"/></svg>
          +1-907-555-0143
        </li>
        <li>
          <svg viewBox="0 0 10 10" aria-hidden="true"><rect x="0.5" y="2" width="9" height="6" fill="none" stroke="#fff"/><path d="M.5 2L5 5.5 9.5 2" fill="none" stroke="#fff"/></svg>
          mkorhonen@tundrabridgeadvisory.example
        </li>
        <li>
          <svg viewBox="0 0 10 10" aria-hidden="true"><circle cx="5" cy="5" r="4.5" fill="none" stroke="#fff"/><ellipse cx="5" cy="5" rx="2" ry="4.5" fill="none" stroke="#fff" stroke-width=".8"/><path d="M.5 5h9" stroke="#fff" stroke-width=".8"/></svg>
          www.coastaltundrabridgeadvisory.example
        </li>
      </ul>
    </div>
    <p class="address">PO Box 418259 Quillwater, Alaska 99642</p>
  </section>

  <section class="card card-back">
    <div class="brand-large">Coastal Tundrabridge<br>Advisory</div>
    <div class="services">
      <h2 class="services-title">OUR SERVICES</h2>
      <p class="services-text">We provide specialized permafrost services to the mining, transportation, and oil &amp; gas industries</p>
    </div>
  </section>
</main>
</body>
</html>
```